Wordpress Design Project for Bankruptcy Law Office in San Francisco

our current website: www.dorvanelilaw-example.com

we would like to re-design it for wordpress to make it faster and a bit more modern.

content should be similar to what we have there right now but also we do family law

please include logo for law office:

Law Office of Marta K. Dolvenidze

Thank you.
Updates

please see attached word document with logos that we like as an example.

we do tend to like color red.  darker red.

Please submit your design variations and logo as soon as possible.   We would like to go over them and make our decision

Reason: Please create couple of more variations of logo for your design, so we can make our decision what we like the most. Please see word doc for samples: Text: Law Office Of Marta K. Dolvenidze

Reason: final touches

Target Market(s)

bankruptcy and family law clients

Industry/Entity Type

Family Law

Requirements
Must have
• see examples of law sites
http://promo.lexorbin-example.com/testimonials

- new logo: Law Office of Marta K. Dolvenidze
- client intake form
- blog
- contact us form

Nice to have
• - map
- red color
- on the front page a nice photo of SF or a happy family

```html
<!DOCTYPE html>
<html lang="en">
<head>
<meta charset="utf-8">
<title>MKD Law 552 – Complete Bankruptcy Information</title>
<link rel="stylesheet" href="https://fonts.googleapis.com/css2?family=Source+Sans+3:ital,wght@0,400;0,600;0,700;1,400&display=swap">
<style>
:root{
  --navy:#1d4e70;
  --navy-dark:#163c58;
  --navy-deep:#12344d;
  --nav-top:#2d6a92;
  --nav-bottom:#1c4d6f;
  --text:#333;
  --link:#1d5f86;
  --title:#1a4f74;
  --band:#f2f2f2;
  --footer:#e6e6e6;
  --white:#fff;
}
*{box-sizing:border-box;margin:0;padding:0}
html,body{width:712px;height:1200px;overflow:hidden;background:var(--white)}
body{font-family:"Source Sans 3",sans-serif;color:var(--text);position:relative}
.top-rule{height:3px;background:var(--navy-dark)}
.site-header{height:86px;position:relative}
.brand{position:absolute;left:22px;top:26px;font-size:34px;font-weight:700;color:var(--navy);letter-spacing:-1px}
.lang{position:absolute;right:20px;top:16px;display:flex;align-items:center;gap:5px;font-size:9px;color:var(--link)}
.lang .select{width:77px;height:17px;background:#dfe8ef;border:1px solid #c9d6e0;color:#1d4e70;padding:2px 5px;display:flex;justify-content:space-between;align-items:center;font-size:8px}
.call{position:absolute;right:20px;top:55px;font-size:11px;color:var(--link);text-transform:uppercase}
.call strong{font-size:16px;font-weight:400;color:#111;margin-left:4px;text-transform:none}
.main-nav{height:30px;background:linear-gradient(var(--nav-top),var(--nav-bottom));display:flex;padding-left:10px}
.main-nav a{color:var(--white);text-decoration:none;font-size:10px;line-height:30px;padding:0 16px;border-right:1px solid rgba(255,255,255,.25);text-transform:uppercase}
.main-nav a:last-child{border-right:0}
.hero{height:245px;background:linear-gradient(180deg,#b7cfe4 0%,#d7e3ec 40%,#6c7b86 70%,#3e4a52 100%)}
.services{height:174px;background:var(--band);display:flex;padding:14px 0 0 14px;gap:18px}
.service{width:160px}
.service h3{font-size:11px;font-weight:600;color:#111;margin:0 0 6px 3px}
.service .thumb{height:66px;border:2px solid var(--white);box-shadow:0 0 2px rgba(0,0,0,.4)}
.service h4{font-size:9.5px;font-weight:700;color:var(--title);margin:8px 0 1px 2px}
.service p{font-size:8px;line-height:11.5px;color:var(--link);margin-left:2px}
.main{display:flex;height:612px}
.content{width:506px;padding:16px 20px 0 12px}
.content h1{font-size:11px;font-weight:600;color:#111;margin-bottom:9px}
.content p{font-size:7.6px;line-height:12.5px;margin-bottom:4px}
.content h5{font-size:7.6px;font-weight:700;margin:4px 0 3px}
.divider{border-top:1px dotted #9aa;margin:14px 0 14px}
.content h2{font-size:11px;font-weight:600;color:#111;margin:0 0 10px 4px}
.story{display:flex;gap:10px}
.story .pic{flex:0 0 152px;height:101px}
.story h3{font-size:9.5px;font-weight:600;color:var(--title);margin-bottom:3px}
.story-tail{margin:8px 0 18px}
.sidebar{width:206px;background:var(--navy);color:var(--white)}
.sidebar h2{height:30px;background:var(--navy-dark);font-weight:400;font-variant:small-caps;font-size:14px;padding:5px 12px;border-bottom:2px solid #2e6b95}
.form{padding:5px 12px 14px}
.form label{display:block;font-size:8.5px;margin:4px 0 2px}
.form .field{height:17px;background:var(--white)}
.form .area{height:47px;background:var(--white)}
.copy{display:flex;align-items:center;gap:5px;font-size:7.6px;margin:8px 0 10px 2px}
.copy span.box{width:8px;height:8px;background:#dde;display:inline-block}
.btns{display:flex;gap:12px}
.btns span{background:var(--navy-deep);font-size:8px;font-weight:600;padding:4px 10px;border-radius:2px}
.news{padding:6px 14px}
.news article{margin-bottom:14px}
.news h3{font-size:9.5px;font-weight:400;margin-bottom:2px}
.news p{font-size:7.6px;line-height:11px;font-style:italic;color:#dbe6ee;margin-bottom:4px}
.news a{font-size:7.6px;font-weight:700;color:var(--white);text-decoration:none}
.site-footer{height:50px;background:var(--footer);display:flex;justify-content:space-between;align-items:center;padding:0 20px 0 14px;font-size:7.6px;color:#222}
</style>
</head>
<body>
<div class="top-rule"></div>
<header class="site-header">
  <div class="brand">mkdlaw552.com</div>
  <div class="lang">Select Language <span class="select">English <svg width="6" height="4"><path d="M0 0h6L3 4z" fill="#1d4e70"/></svg></span></div>
  <div class="call">Call us now: <strong>(555) 014-2290</strong></div>
</header>
<nav class="main-nav">
  <a href="#">Home</a><a href="#">About Us</a><a href="#">Areas of Practise</a><a href="#">Resources</a><a href="#">Blog</a><a href="#">FAQ</a><a href="#">Contact Us</a>
</nav>
<div class="hero" role="img" aria-label="City skyline with glass towers under a pale blue sky"></div>

<section class="services">
  <div class="service"><h3>Debt Relief</h3><div class="thumb" role="img" aria-label="Relieved man lying on grass among papers" style="background:linear-gradient(#7a9a4a,#c9d0c4)"></div><h4>Tittle goes here</h4><p>Lorem ipsum dolor sit amet, consectetur adipisicing elit, sed do eiusmod tempor incididunt ut labore et dolore magna</p></div>
  <div class="service"><h3>Fore Closure Prevention</h3><div class="thumb" role="img" aria-label="For sale sign in front of a white picket fence" style="background:linear-gradient(90deg,#5a5a55,#c3283a 45%,#d6d0c6)"></div><h4>Tittle goes here</h4><p>Lorem ipsum dolor sit amet, consectetur adipisicing elit, sed do eiusmod tempor incididunt ut labore et dolore magna</p></div>
  <div class="service"><h3>Chapter 13</h3><div class="thumb" role="img" aria-label="Open law book on a desk" style="background:linear-gradient(#5a2c18,#c9a98a 55%,#6b3a22)"></div><h4>Tittle goes here</h4><p>Lorem ipsum dolor sit amet, consectetur adipisicing elit, sed do eiusmod tempor incididunt ut labore et dolore magna</p></div>
  <div class="service"><h3>Chapter 7</h3><div class="thumb" role="img" aria-label="Row of leather bound law books" style="background:linear-gradient(90deg,#2b1a12,#8a4a2a 50%,#3a2418)"></div><h4>Tittle goes here</h4><p>Lorem ipsum dolor sit amet, consectetur adipisicing elit, sed do eiusmod tempor incididunt ut labore et dolore magna</p></div>
</section>

<div class="main">
  <main class="content">
    <h1>WELCOME TO MKD LAW 552 - COMPLETE BANKRUPTCY INFORMATION</h1>
    <p>The Law Offices of Marta K. Dolvenidze is a consumer law office dedicated to consumer protection and zealously defending the rights of our clients. We offer the big firm quality legal representation with a small firm individualized attention to each client.</p>
    <p>Our office offers services in: all types of consumer bankruptcy filings, i.e. Chapter 7, Chapter 13, Chapter 11, negotiating a settlement of your debts, assisting you in the defense of collection litigation and defending you against foreclosure. Please review our site and see what we may be able to offer you. Feel free to call us at (555) 017-3388 or use our free case evaluation form.</p>
    <h5>Speak to a Lawyer</h5>
    <p>Unlike some other law firms, when you call the Law Office of Marta K. Dolvenidze you will speak to an actual attorney. Not a paralegal or assistant. And even after retaining our office you will still speak to an attorney unlike other firms where you cannot get a hold of your attorney after several attempts.</p>
    <p style="margin-top:8px">Lorem ipsum dolor sit amet, consectetuer adipiscing elit. Nam cursus. Morbi ut mi. Nullam enim leo, egestas id, condimentum at, laoreet mattis, massa. Sed eleifend nonummy diam. Praesent mauris ante, elementum et, bibendum at, posuere sit amet, nibh. Duis tincidunt lectus quis dui viverra vestibulum. Suspendisse vulputate aliquam dui. Nulla elementum dui ut augue. Aliquam vehicula mi at mauris. Maecenas placerat, nisl at consequat rhoncus, sem nunc gravida justo, quis eleifend arcu velit quis lacus. Morbi magna magna, tincidunt a, mattis non, imperdiet vitae</p>
    <div class="divider"></div>
    <h2>STORIES &amp; MORE INFORMATION</h2>
    <div class="story">
      <div class="pic" role="img" aria-label="Judge's gavel resting on a law book" style="background:linear-gradient(135deg,#2a1208,#8a4a24 55%,#3a1a0c)"></div>
      <div><h3>Story TItle line goes here</h3>
      <p>Lorem ipsum dolor sit amet, consectetuer adipiscing elit. Nam cursus. Morbi ut mi. Nullam enim leo, egestas id, condimentum at, laoreet mattis, massa.</p>
      <p>Sed eleifend nonummy diam. Praesent mauris ante, elementum et, bibendum at, posuere sit amet, nibh. Duis tincidunt lectus quis dui viverra vestibulum. Suspendisse vulputate aliquam dui. Nulla elementum dui ut augue. Aliquam vehicula mi at mauris. Maecenas placerat, nisl at consequat rhoncus, sem nunc gravida justo, quis eleifend arcu velit quis lacus. Morbi magna magna, tincidunt a, mattis non, imperdiet vitae, tellus.</p></div>
    </div>
    <p class="story-tail">Mauris vel lacus vitae felis vestibulum volutpat. Etiam est nunc, venenatis in, tristique eu, imperdiet ac, nisl. Cum sociis natoque penatibus et magnis dis parturient montes, nascetur ridiculus mus. In iaculis facilisis massa.</p>
    <div class="story">
      <div class="pic" role="img" aria-label="Happy family with children on bicycles in a park" style="background:linear-gradient(135deg,#6f8a3a,#b9c98a 50%,#a8304a)"></div>
      <div><h3>Story TItle line goes here</h3>
      <p>Lorem ipsum dolor sit amet, consectetuer adipiscing elit. Nam cursus. Morbi ut mi. Nullam enim leo, egestas id, condimentum at, laoreet mattis, massa.</p>
      <p>Sed eleifend nonummy diam. Praesent mauris ante, elementum et, bibendum at, posuere sit amet, nibh. Duis tincidunt lectus quis dui viverra vestibulum. Suspendisse vulputate aliquam dui. Nulla elementum dui ut augue. Aliquam vehicula mi at mauris. Maecenas placerat, nisl at consequat rhoncus, sem nunc gravida justo, quis eleifend arcu velit quis lacus. Morbi magna magna, tincidunt a, mattis non, imperdiet vitae, tellus.</p></div>
    </div>
    <p class="story-tail">Mauris vel lacus vitae felis vestibulum volutpat. Etiam est nunc, venenatis in, tristique eu, imperdiet ac, nisl. Cum sociis natoque penatibus et magnis dis parturient montes, nascetur ridiculus mus. In iaculis facilisis massa.</p>
  </main>

  <aside class="sidebar">
    <h2>Contact Form</h2>
    <div class="form">
      <label>Name:</label><div class="field"></div>
      <label>Email:</label><div class="field"></div>
      <label>Phone:</label><div class="field"></div>
      <label>Subject:</label><div class="field"></div>
      <label>Message:</label><div class="area"></div>
      <div class="copy"><span class="box"></span>Send a copy of this message to yourself</div>
      <div class="btns"><span>SEND</span><span>RESET</span></div>
    </div>
    <h2>Recent Blog &amp; News</h2>
    <div class="news">
      <article><h3>Tittle line here</h3><p>Lorem ipsum dolor sit amet, consectetuer adipiscing elit. Nam cursus. Morbi ut mi. Nullam enim leo, egestas id, condimentum at, laoreet mattis, massa.</p><a href="#">LEARN MORE</a></article>
      <article><h3>Tittle line here</h3><p>Lorem ipsum dolor sit amet, consectetuer adipiscing elit. Nam cursus. Morbi ut mi. Nullam enim leo, egestas id, condimentum at, laoreet mattis, massa.</p><a href="#">LEARN MORE</a></article>
      <article><h3>Tittle line here</h3><p>Proin dui lectus, cursus eu, mattis laoreet, viverra sit amet, quam. Curabitur vel dolor ultrices ipsum dictum tristique. Praesent vitae lacus. Ut velit enim, vestibulum non, fermentum nec, hendrerit quis, leo. Pellentesque rutrum malesuada neque.</p><a href="#">LEARN MORE</a></article>
    </div>
  </aside>
</div>

<footer class="site-footer">
  <span>© 2012 Company Name &nbsp;|&nbsp; All right reserved &nbsp;|&nbsp; Term &amp; Conditions</span>
  <span>HOME &nbsp;|&nbsp; ABOUT US &nbsp;|&nbsp; AREAS OF PRACTISE &nbsp;|&nbsp; RESOURCES &nbsp;|&nbsp; BLOG &nbsp;|&nbsp; FAQ &nbsp;|&nbsp; CONTACT US</span>
</footer>
</body>
</html>
```